Stationary Set Rebrand for Brennick

We are a Canadian Distribution and Service Company that was established in 1969. Over the past 5 decades we have expanded our business and have warehouses across Canada. We specialize in adhesive tapes, adhesives, films, safety, warehouse, shipping, janitorial and packaging supplies.

We have updated our logo design and would like a new corporate branding identity that includes a new fresh Stationary Set (Business Cards, Letterhead, Letterhead MS Word, Envelope, Presentation Folders, Email Signatures, Notepad Covers, etc.)

Target Market(s)

Industrial Business Sector

Font styles to use
Sans Serif

Colors
0054AA
0677BA
7BADD7
CADEEF
E8F1F8
0094D4
00A9DD
6FCCEA
C7EBF8
E9F6FB
00AB8E
00BBA5
67D7C9
C6EFE9
E9F9F6
EB3D1F
EC4F4E
F09395
F8D3D4
FCEDEE

Requirements
Should not have
• Colors not too light, darker colours preferred

```html
<!DOCTYPE html>
<html lang="en">
<head>
<meta charset="utf-8">
<title>Brennick Business Card</title>
<link rel="stylesheet" href="https://fonts.googleapis.com/css2?family=Archivo+Narrow:wght@700&family=Montserrat:wght@300;400;700;800&display=swap">
<style>
  :root {
    --stage: #4e4e4e;
    --card: #161616;
    --ink-light: #ffffff;
    --accent-red: #d92027;
    --leaf-light: #e6e6e6;
    --leaf-mid: #7a7a7a;
    --leaf-dark: #0d0d0d;
  }
  * { box-sizing: border-box; margin: 0; padding: 0; }
  html, body {
    width: 1200px;
    height: 801px;
    overflow: hidden;
  }
  body {
    background: var(--stage);
    position: relative;
    font-family: "Montserrat", sans-serif;
  }
  .card {
    position: absolute;
    top: 246px;
    width: 540px;
    height: 309px;
    background: var(--card);
    box-shadow: 0 3px 0 var(--accent-red), 0 14px 28px rgba(0, 0, 0, 0.35);
    overflow: hidden;
  }
  .card--front { left: 40px; }
  .card--back { left: 620px; }

  .wordmark {
    position: absolute;
    top: 30px;
    left: 34px;
    font-family: "Montserrat", sans-serif;
    font-weight: 800;
    font-size: 78px;
    line-height: 1;
    letter-spacing: -2px;
    color: var(--ink-light);
    display: flex;
    align-items: center;
    gap: 12px;
  }
  .wordmark__dot {
    width: 16px;
    height: 16px;
    border-radius: 50%;
    background: var(--accent-red);
    margin-top: 30px;
  }
  .tagline {
    position: absolute;
    top: 116px;
    left: 36px;
    font-family: "Archivo Narrow", sans-serif;
    font-weight: 700;
    font-size: 23px;
    color: var(--ink-light);
    letter-spacing: 0.3px;
  }
  .person {
    position: absolute;
    top: 178px;
    left: 36px;
  }
  .person__name {
    font-weight: 700;
    font-size: 26px;
    color: var(--accent-red);
    line-height: 1.1;
  }
  .person__title {
    font-weight: 300;
    font-size: 14px;
    color: var(--ink-light);
    margin-top: 4px;
    letter-spacing: 0.4px;
  }
  .divider {
    position: absolute;
    top: 176px;
    left: 300px;
    width: 1.5px;
    height: 60px;
    background: var(--accent-red);
  }
  .contacts {
    position: absolute;
    top: 174px;
    left: 316px;
    list-style: none;
  }
  .contacts__item {
    display: flex;
    align-items: center;
    gap: 8px;
    font-weight: 400;
    font-size: 12.5px;
    line-height: 21px;
    color: var(--ink-light);
  }
  .contacts__icon {
    width: 11px;
    height: 11px;
    flex: none;
  }
  .address {
    position: absolute;
    bottom: 28px;
    left: 36px;
    font-weight: 300;
    font-size: 13px;
    color: var(--ink-light);
    letter-spacing: 0.4px;
  }

  .leaf-field {
    position: absolute;
    inset: 0;
    background: linear-gradient(100deg, var(--leaf-light) 0%, #bdbdbd 22%, var(--leaf-mid) 40%, #262626 58%, var(--leaf-dark) 100%);
  }
</style>
</head>
<body>
  <section class="card card--front" aria-label="Business card front">
    <div class="wordmark">Brennick<span class="wordmark__dot"></span></div>
    <p class="tagline">Tape and Packaging Specialists</p>

    <div class="person">
      <p class="person__name">Daniel Harcourt</p>
      <p class="person__title">Managing Director</p>
    </div>

    <div class="divider"></div>

    <ul class="contacts">
      <li class="contacts__item">
        <svg class="contacts__icon" viewBox="0 0 12 12" aria-hidden="true"><path fill="#d92027" d="M2.4 0.6 4.2 2.8 3.2 4.2C3.8 5.8 5.2 7.4 7.8 8.8L9.2 7.8 11.4 9.6 10.2 11.4C5.4 11 1 6.6 0.6 1.8Z"/></svg>
        123 456 789
      </li>
      <li class="contacts__item">
        <svg class="contacts__icon" viewBox="0 0 12 12" aria-hidden="true"><rect x="0.5" y="2" width="11" height="8" fill="#d92027"/><path d="M0.5 2 6 6.6 11.5 2" fill="none" stroke="#161616" stroke-width="1"/></svg>
        info@brennickmail.com
      </li>
      <li class="contacts__item">
        <svg class="contacts__icon" viewBox="0 0 12 12" aria-hidden="true"><circle cx="6" cy="6" r="5.5" fill="#d92027"/><path d="M0.5 6H11.5M6 0.5C3.8 3 3.8 9 6 11.5M6 0.5C8.2 3 8.2 9 6 11.5" fill="none" stroke="#161616" stroke-width="0.8"/></svg>
        www.brennickwebsite.com
      </li>
    </ul>

    <p class="address">Your address, City State, Zip 1234</p>
  </section>

  <section class="card card--back" aria-label="Business card back">
    <div class="leaf-field" role="img" aria-label="Repeating maple leaf pattern fading from silver to black, with a single red leaf"></div>
  </section>
</body>
</html>
```